Copper lark buildworks

Copper lark buildworks is a small construction company.
Who is a licenced builder, Carpenter, joiner,
working on heritage ,new build, speacial projects and sometimes furniture

Industry/Entity Type

Construction

```html
<!DOCTYPE html>
<html lang="en">
<head>
<meta charset="utf-8">
<title>Copper lark buildworks — Business Card</title>
<link rel="stylesheet" href="https://fonts.googleapis.com/css2?family=Oswald:wght@500&family=Arimo:wght@400&display=swap">
<style>
  :root {
    --page-bg: #d9d6d1;
    --card-bg: #1f1f1f;
    --card-bg-light: #262626;
    --brand-green: #3d9e47;
    --text-light: #e6e6e6;
    --divider: #9a9a9a;
  }
  html, body {
    margin: 0;
    padding: 0;
    width: 1200px;
    height: 900px;
    overflow: hidden;
    background: var(--page-bg);
  }
  .canvas {
    position: relative;
    width: 1200px;
    height: 900px;
  }
  .business-card {
    position: absolute;
    left: 150px;
    top: 193px;
    width: 900px;
    height: 514px;
    border-radius: 26px;
    background: radial-gradient(ellipse at 40% 35%, var(--card-bg-light), var(--card-bg) 70%);
    box-shadow: 0 10px 30px rgba(0,0,0,0.25);
  }
  .company-name {
    position: absolute;
    left: 110px;
    top: 150px;
    margin: 0;
    font-family: 'Oswald', sans-serif;
    font-weight: 500;
    font-size: 56px;
    letter-spacing: -0.5px;
    color: var(--brand-green);
  }
  .contact-row {
    position: absolute;
    left: 195px;
    top: 352px;
    display: flex;
    align-items: center;
  }
  .accent-square {
    width: 30px;
    height: 30px;
    background: var(--brand-green);
    margin-right: 26px;
    align-self: flex-end;
    margin-bottom: -14px;
  }
  .contact-name {
    font-family: 'Oswald', sans-serif;
    font-weight: 500;
    font-size: 40px;
    color: var(--brand-green);
  }
  .contact-divider {
    font-family: 'Arimo', sans-serif;
    font-size: 26px;
    color: var(--divider);
    margin: 0 22px;
  }
  .contact-phone {
    font-family: 'Arimo', sans-serif;
    font-size: 36px;
    letter-spacing: 1px;
    color: var(--text-light);
  }
</style>
</head>
<body>
  <main class="canvas">
    <section class="business-card">
      <h1 class="company-name">Copper lark buildworks</h1>
      <div class="contact-row">
        <span class="accent-square"></span>
        <span class="contact-name">Maren Holt</span>
        <span class="contact-divider">|</span>
        <span class="contact-phone">0491570156</span>
      </div>
    </section>
  </main>
</body>
</html>
```